-Photo booth rental Web Design Project

Our business is a small photo booth rental service serving the capital region and surrounding areas. The photo booth is a portable booth that fits up to 10 guest. I am looking for a website that will have social media capabilities and also private log ins for clients to view their photo albums online after their event. We provide full service photo booth rentals for all types of parties. I am looking for something fun and unique but also professional and I am also looking to maybe somehow incorporate the age of the photo booth which was invented in 1888. I do not have the photos of our photo booth available because we are just starting up and I wanted to get everything together first but I will provide stock photo booth pictures .Thank you for your patience i know it wont be an easy task with out those things. I added a word document describing information i will need on our website, i am looking for a home page, contact us and book an event page, online gallery page, and pricing. If you need any more information please feel free to contact me. Thanks for your help and I look forward to working with you.

Target Market(s)

For everyone from brides to be for their weddings or private parties, corporate parties, school dances, charity events, community events ect

Industry/Entity Type

Business

Requirements
Nice to have
• social media sharing

```html
<!DOCTYPE html>
<html lang="en">
<head>
<meta charset="utf-8">
<title>Giggle Frames Photo Booth</title>
<link href="https://fonts.googleapis.com/css2?family=Alegreya+Sans:wght@400;500;700&family=Oswald:wght@600&family=Lato:wght@300;700&display=swap" rel="stylesheet">
<style>
:root{
  --page:#efeeed;
  --brown:#4f3325;
  --brown-dark:#3a2419;
  --brown-text:#3b2418;
  --body-text:#5b5b5b;
  --white:#ffffff;
  --orange-top:#f2793a;
  --orange-bot:#e9501f;
  --blue-top:#2a8fcf;
  --blue-bot:#1668ad;
  --yellow-top:#f4bd31;
  --yellow-bot:#eda31b;
}
*{margin:0;padding:0;box-sizing:border-box}
html,body{width:1200px;height:2203px;overflow:hidden}
body{background:var(--page);font-family:"Alegreya Sans",sans-serif;position:relative;color:var(--body-text)}
.abs{position:absolute}
.brand{left:0;width:1200px;top:42px;text-align:center;color:var(--brown-text);font-family:"Alegreya Sans",sans-serif;font-weight:500;font-size:44px;line-height:46px}
.brand span{display:block}
.nav-bar{left:0;top:181px;width:1200px;height:73px;background:linear-gradient(var(--brown),var(--brown-dark))}
.nav-bar a,.footer-nav a{position:absolute;color:var(--white);text-decoration:none;font-size:16px;text-transform:uppercase;top:26px;white-space:nowrap}
.hero{left:0;top:254px;width:1200px;height:454px;background:linear-gradient(100deg,#3c3a34 0%,#6b6a5a 35%,#8a8a6a 60%,#9d917b 80%,#6d6a5b 100%)}
.hero-title{left:0;width:1200px;top:350px;text-align:center;font-family:"Oswald",sans-serif;font-weight:600;font-size:64px;color:var(--white);letter-spacing:0}
.hero-sub{left:0;width:1200px;top:457px;text-align:center;font-size:21px;color:var(--white)}
.hero-btn{left:501px;top:521px;width:200px;height:80px;border:1px solid var(--white);border-radius:2px;color:var(--white);font-size:21px;display:flex;align-items:center;justify-content:center}
.dot{top:652px;width:12px;height:12px;border:1px solid var(--white);border-radius:50%}
.dot.on{background:radial-gradient(var(--white) 35%,transparent 40%)}
.section-head{font-weight:700;color:var(--brown-text);font-size:28px}
.booth-img{left:88px;top:815px;width:238px;height:287px;background:linear-gradient(90deg,#1a1a1a,#b3161b 45%,#1a1a1a);border-radius:4px}
.welcome-text{left:360px;top:845px;width:720px;font-size:11.5px;line-height:20.5px}
.welcome-text p+p{margin-top:12px}
.btn-dark{left:358px;top:996px;width:112px;height:54px;background:var(--brown-dark);color:var(--white);font-size:12px;display:flex;align-items:center;justify-content:center;border-radius:2px;box-shadow:0 2px 0 #1f120b}
.service-img{top:1241px;width:324px;height:184px}
.service-title{top:1455px;font-weight:500;font-size:18px;color:var(--brown-text)}
.service-desc{top:1486px;font-size:10px;color:#444}
.price{top:1630px;width:322px;height:155px;border-radius:2px;color:var(--white);text-align:center}
.price .name{font-family:"Lato",sans-serif;font-weight:300;font-size:30px;margin-top:40px}
.price .amount{font-family:"Lato",sans-serif;font-weight:700;font-size:26px;margin-top:10px}
.standard{left:84px;background:linear-gradient(var(--orange-top),var(--orange-bot))}
.ultimate{left:439px;background:linear-gradient(var(--blue-top),var(--blue-bot))}
.extreme{left:798px;background:linear-gradient(var(--yellow-top),var(--yellow-bot))}
.addons{left:84px;top:1823px;width:1037px;height:104px;background:linear-gradient(var(--brown),var(--brown-dark));color:var(--white);font-size:14.5px;text-align:center;line-height:27px;padding-top:25px}
.footer{left:0;top:1976px;width:1200px;height:227px;background:var(--brown)}
.footer-nav a{top:48px}
.social{top:101px;width:36px;height:36px;border:2px solid var(--white);border-radius:50%}
.copyright{left:0;width:1200px;top:170px;text-align:center;color:var(--white);font-size:11px}
</style>
</head>
<body>
  <div class="abs brand"><span>Giggle Frames</span><span>photo booth</span></div>

  <nav class="abs nav-bar">
    <a href="#" style="left:85px">Home</a>
    <a href="#" style="left:184px">Pricing</a>
    <a href="#" style="left:295px">Contact Us</a>
    <a href="#" style="left:436px">Book an Event</a>
    <a href="#" style="left:604px">Client Log In</a>
  </nav>

  <div class="abs hero" role="img" aria-label="Photographer holding a camera at a wedding, guests blurred in the background"></div>
  <h1 class="abs hero-title">FAMILY OWNED AND OPERATED PHOTO BOOTH</h1>
  <div class="abs hero-sub">SERVING COLUMBIA, GREENE, ALBANY &amp;SURROUNDING COUNTIES</div>
  <div class="abs hero-btn">BOOK AN EVENT</div>
  <span class="abs dot" style="left:572px"></span>
  <span class="abs dot on" style="left:594px"></span>
  <span class="abs dot" style="left:616px"></span>

  <h2 class="abs section-head" style="left:0;width:1200px;text-align:center;top:756px">WELCOME TO&nbsp; GIGGLE FRAMES</h2>
  <div class="abs booth-img" role="img" aria-label="Portable photo booth with a couple standing in front of it"></div>
  <div class="abs welcome-text">
    <p>We are a family owned and operated photo booth rental company serving Columbia, Greene, Albany &amp; surrounding counties to create fun &amp; memorable memories for any type of event.</p>
    <p>Fun entertainment &amp; favors for all event types, ex: weddings, birthday parties, graduations, holiday parties, corporate parties, bar/ bat mitzvahs, bridal showers, baby showers, anniversaries, grand openings, school events, proms, corporate events, promotional events, trade shows, conventions, community &amp; charity events</p>
  </div>
  <div class="abs btn-dark">READ MORE</div>

  <h2 class="abs section-head" style="left:84px;top:1159px">OUR SERVICES</h2>
  <div class="abs service-img" style="left:84px;background:linear-gradient(135deg,#f7a21b,#e8611b 40%,#6a2b6e 75%,#1c2a6b)" role="img" aria-label="Concert crowd with raised hands under stage lights"></div>
  <div class="abs service-img" style="left:441px;background:linear-gradient(135deg,#3b1a5a,#a0389c 50%,#e07ab8 75%,#5a2a6a)" role="img" aria-label="Microphone on a stand under purple stage light"></div>
  <div class="abs service-img" style="left:796px;background:linear-gradient(135deg,#5a6a3a,#c8c2b8 40%,#7a1a1a 70%,#2a2a2a)" role="img" aria-label="Wedding couple riding in a carriage"></div>
  <div class="abs service-title" style="left:82px">SED UT PERSPICIATIS</div>
  <div class="abs service-desc" style="left:84px">Sed do eiusmod tempor incididunt ut labore et dolore</div>
  <div class="abs service-title" style="left:440px">SED UT PERSPICIATIS</div>
  <div class="abs service-desc" style="left:441px">Sed do eiusmod tempor incididunt ut labore et dolore</div>
  <div class="abs service-title" style="left:793px">SED UT PERSPICIATIS</div>
  <div class="abs service-desc" style="left:793px">Sed do eiusmod tempor incididunt ut labore et dolore</div>

  <h2 class="abs section-head" style="left:84px;top:1547px">OUR PRICING</h2>
  <div class="abs price standard"><div class="name">STANDARD</div><div class="amount">$675</div></div>
  <div class="abs price ultimate"><div class="name">ULTIMATE</div><div class="amount">$850</div></div>
  <div class="abs price extreme"><div class="name">EXTREME</div><div class="amount">$975</div></div>
  <div class="abs addons">ADD ON'S: MAGNET PHOTO STRIP FRAMES, STAND UP ACRYLICPHOTO STRIP FRAMES,<br>ONLY $100 DEPOSIT</div>

  <footer class="abs footer">
    <nav class="footer-nav">
      <a href="#" style="left:291px">Home</a>
      <a href="#" style="left:389px">Pricing</a>
      <a href="#" style="left:501px">Contact Us</a>
      <a href="#" style="left:642px">Book an Event</a>
      <a href="#" style="left:809px">Client Log In</a>
    </nav>
    <span class="abs social" style="left:487px" aria-label="Social link"></span>
    <span class="abs social" style="left:534px" aria-label="Social link"></span>
    <span class="abs social" style="left:581px" aria-label="Social link"></span>
    <span class="abs social" style="left:628px" aria-label="Social link"></span>
    <span class="abs social" style="left:675px" aria-label="Social link"></span>
    <div class="abs copyright">©2014 Giggle Frames. All rights reserved.</div>
  </footer>
</body>
</html>
```